Private Investigation Business Card Design

I need a business card for a new private investigation company named Brisk Inquiries. I perform mainly surveillance jobs, vehicle repossessions, document serves etc. The final design should aim for a professional look. The logo has a magnifying glass with stick man arms and legs and is in a running action to show the "Brisk" aspect of the name. If the colour scheme could remain the same as the website www.briskinquiries-demo.com.au with silvers,blacks and a couple electric blue highlights.
Industry/Entity Type
Business
Contact Information for Business Card
Morgan Kellaway
Brisk Inquiries
0487316204
PO Box 58, Carnwell NSW 2291
info@briskinquiries-demo.com.au
www.briskinquiries-demo.com.au
Look and feel

```html
<!DOCTYPE html>
<html lang="en">
<head>
<meta charset="utf-8">
<title>Brisk Inquiries – Business Card</title>
<link rel="stylesheet" href="https://fonts.googleapis.com/css2?family=Source+Sans+3:wght@400;600;700&display=swap">
<style>
  :root {
    --page-bg: #e6e6e8;
    --card-top: #fbfbfb;
    --card-bottom: #eeeeef;
    --card-edge: #ffffff;
    --ink: #1c1c1c;
    --name-grey: #8c8c8c;
    --brand-grey: #5a5a5c;
    --mark-silver: #b9bbbf;
    --rule-grey: #b5b5b7;
    --icon-grey: #8e8e90;
  }
  * { margin: 0; padding: 0; box-sizing: border-box; }
  html, body {
    width: 1200px;
    height: 900px;
    overflow: hidden;
    background: var(--page-bg);
    font-family: "Source Sans 3", "Myriad Pro", sans-serif;
  }
  .canvas {
    position: relative;
    width: 1200px;
    height: 900px;
  }
  .card {
    position: absolute;
    left: 160px;
    top: 180px;
    width: 880px;
    height: 540px;
    border-radius: 22px;
    background: linear-gradient(170deg, var(--card-top) 0%, var(--card-bottom) 100%);
    border: 3px solid var(--card-edge);
    box-shadow: 0 10px 30px rgba(0, 0, 0, 0.12);
    overflow: hidden;
  }
  .brand {
    position: absolute;
    right: 60px;
    top: 62px;
    display: flex;
    align-items: center;
    gap: 26px;
  }
  .brand-name {
    font-size: 66px;
    font-weight: 600;
    color: var(--brand-grey);
    letter-spacing: 1px;
    line-height: 1;
  }
  .brand-dot {
    width: 74px;
    height: 74px;
    border-radius: 50%;
    background: var(--mark-silver);
  }
  .holder {
    position: absolute;
    left: 34px;
    top: 276px;
  }
  .holder-name {
    font-size: 28px;
    font-weight: 700;
    color: var(--name-grey);
    line-height: 1.15;
  }
  .holder-company {
    font-size: 23px;
    font-weight: 400;
    color: var(--ink);
    line-height: 1.3;
  }
  .rule {
    position: absolute;
    left: 330px;
    right: 0;
    top: 315px;
    height: 1px;
    background: linear-gradient(90deg, rgba(181,181,183,0) 0%, var(--rule-grey) 25%, var(--rule-grey) 100%);
  }
  .contacts {
    position: absolute;
    right: 48px;
    top: 340px;
    list-style: none;
    text-align: right;
  }
  .contact {
    display: flex;
    justify-content: flex-end;
    align-items: center;
    gap: 12px;
    font-size: 22px;
    color: var(--ink);
    height: 35px;
  }
  .contact-icon {
    width: 18px;
    height: 18px;
    flex: none;
  }
  .contact--address {
    margin-top: 10px;
    padding-right: 0;
  }
</style>
</head>
<body>
<main class="canvas">
  <section class="card">
    <div class="brand">
      <span class="brand-name">Brisk Inquiries</span>
      <span class="brand-dot"></span>
    </div>

    <div class="holder">
      <p class="holder-name">Morgan Kellaway</p>
      <p class="holder-company">Brisk Inquiries</p>
    </div>

    <div class="rule"></div>

    <ul class="contacts">
      <li class="contact">
        <span>0487316204</span>
        <svg class="contact-icon" viewBox="0 0 18 18" aria-hidden="true">
          <path d="M2 7 C2 3 16 3 16 7 L13 8 L12 6 C10 5.4 8 5.4 6 6 L5 8 Z" fill="var(--icon-grey)"/>
          <rect x="4" y="9" width="10" height="6" rx="1.5" fill="var(--icon-grey)"/>
        </svg>
      </li>
      <li class="contact">
        <span>info@briskinquiries-demo.com.au</span>
        <svg class="contact-icon" viewBox="0 0 18 18" aria-hidden="true">
          <rect x="2" y="4" width="14" height="10" rx="1" fill="var(--icon-grey)"/>
          <path d="M2.5 4.5 L9 10 L15.5 4.5" fill="none" stroke="#ffffff" stroke-width="1.2"/>
        </svg>
      </li>
      <li class="contact">
        <span>www.briskinquiries-demo.com.au</span>
        <svg class="contact-icon" viewBox="0 0 18 18" aria-hidden="true">
          <rect x="2.5" y="7.5" width="9" height="4" rx="2" transform="rotate(-45 7 9.5)" fill="none" stroke="var(--icon-grey)" stroke-width="1.5"/>
          <rect x="6.5" y="6.5" width="9" height="4" rx="2" transform="rotate(-45 11 8.5)" fill="none" stroke="var(--icon-grey)" stroke-width="1.5"/>
        </svg>
      </li>
      <li class="contact contact--address">
        <span>PO Box 58, Carnwell NSW 2291</span>
      </li>
    </ul>
  </section>
</main>
</body>
</html>
```